History of Bramwell Fixture Services Inc

This is to be a large poster (48" x 16' Landscape Orientation) printed by a large format printer. The poster through text and photos will represent the history of our company. The file called "Timeline List 20150318" has the events by date order. Maybe this shouldn't be under poster but we didn't see another category that applied.
Reason: We needed to better organize the pictures and content. We cut down the number of pictures and "event" to 105 instead of the 300 some it was before.
Reason: Upon request i have extended the deadline. I apologize for any inconvenience. I'm new to pixel forum. Let me know if you have anymore feed back from me.
Target Market(s)
This will be the center piece of our office for both customers and clients to view.
Industry/Entity Type
Landscape
Look and feel
Each slider illustrates characteristics of the customer's brand and the style your logo design should communicate.

```html
<!DOCTYPE html>
<html lang="en">
<head>
<meta charset="utf-8">
<title>History of Bramwell Fixture Services Inc</title>
<link rel="stylesheet" href="https://fonts.googleapis.com/css2?family=Anton&family=Oswald:wght@700&display=swap">
<style>
:root{
  --page:#e9e6e1;
  --strip:#a8aaae;
  --ink:#111111;
  --pin:#4a4a4e;
  --stem:#2c3a8c;
  --band-1:#5a3a1c;
  --band-2:#141414;
  --band-3:#1c1c6e;
  --band-4:#3a2410;
  --y-gold:#e6c21a;
  --y-yellow:#f5ee1e;
  --y-orange:#f0a040;
  --y-red:#e0201c;
  --y-magenta:#ff1ef0;
  --y-blue:#2a90d0;
  --y-green:#2ee81e;
  --y-cyan:#1ee6f0;
  --y-tan:#c8a070;
  --y-pink:#f0407a;
  --y-teal:#1a90c0;
}
*{box-sizing:border-box;margin:0;padding:0}
html,body{width:1200px;height:1098px;overflow:hidden;background:var(--page)}
.timeline-poster{
  position:absolute;left:66px;top:398px;width:1062px;height:340px;
  display:flex;flex-direction:column;
  box-shadow:0 4px 12px rgba(0,0,0,.25);
}
.era{height:85px;display:flex;flex-direction:column}
.event-strip{
  height:63px;background:var(--strip);
  display:grid;grid-template-columns:repeat(24,1fr);padding:0 3px;overflow:hidden;
}
.event{position:relative;padding-top:8px}
.event-title{
  position:absolute;left:0;top:1px;
  font-family:Oswald,sans-serif;font-weight:700;font-size:5.5px;line-height:6px;color:var(--ink);white-space:nowrap;
}
.event-photo{display:block;width:34px;height:30px;border:1px solid #fff}
.tone-1{background:linear-gradient(135deg,#5b5a86,#c0463a)}
.tone-2{background:linear-gradient(160deg,#4e3a2c,#c9b6a0)}
.tone-3{background:linear-gradient(160deg,#cfd2d8,#f4f4f6)}
.tone-4{background:linear-gradient(135deg,#3e5a78,#d8a060)}
.tone-5{background:linear-gradient(160deg,#6a6a6a,#e0dcd4)}
.tone-6{background:linear-gradient(135deg,#7a3a3a,#e8c8a0)}
.event-marker{display:flex;align-items:flex-start;gap:2px;margin-top:2px}
.pin{width:7px;height:7px;border-radius:50%;background:var(--pin);flex:none;position:relative}
.pin::after{content:"";position:absolute;left:3px;top:7px;width:1px;height:9px;background:var(--stem)}
.event-caption{font-family:Oswald,sans-serif;font-weight:700;font-size:5.5px;line-height:6px;color:var(--ink);width:30px}
.year-band{
  height:22px;display:grid;grid-template-columns:repeat(25,1fr);align-items:center;padding:0 3px;
  font-family:Anton,sans-serif;font-size:14px;text-align:center;
}
.era-1 .year-band{background:var(--band-1)}
.era-2 .year-band{background:var(--band-2)}
.era-3 .year-band{background:var(--band-3)}
.era-4 .year-band{background:var(--band-4)}
.gold{color:var(--y-gold)}.yellow{color:var(--y-yellow)}.orange{color:var(--y-orange)}
.red{color:var(--y-red)}.magenta{color:var(--y-magenta)}.blue{color:var(--y-blue)}
.green{color:var(--y-green)}.cyan{color:var(--y-cyan)}.tan{color:var(--y-tan)}
.pink{color:var(--y-pink)}.teal{color:var(--y-teal)}
</style>
</head>
<body>
<main class="timeline-poster" aria-label="History of Bramwell Fixture Services Inc">

<section class="era era-1">
  <div class="event-strip">
    <div class="event"><span class="event-photo tone-1" role="img" aria-label="Founding day photo"></span><div class="event-marker"><span class="pin"></span><span class="event-caption">Company Founded</span></div></div>
    <div class="event"><span class="event-photo tone-2" role="img" aria-label="First van photo"></span><div class="event-marker"><span class="pin"></span><span class="event-caption">First Van</span></div></div>
    <div class="event"><span class="event-title">First Office</span><span class="event-photo tone-3" role="img" aria-label="First office photo"></span><div class="event-marker"><span class="pin"></span></div></div>
    <div class="event"><span class="event-photo tone-4" role="img" aria-label="Owners photo"></span><div class="event-marker"><span class="pin"></span><span class="event-caption">Dan &amp; Ruth</span></div></div>
    <div class="event"><span class="event-photo tone-5" role="img" aria-label="Contract signing photo"></span><div class="event-marker"><span class="pin"></span><span class="event-caption">Ashford Contract</span></div></div>
    <div class="event"><span class="event-title">Marriage and Kids</span><span class="event-photo tone-6" role="img" aria-label="Family photo"></span><div class="event-marker"><span class="pin"></span></div></div>
    <div class="event"><span class="event-photo tone-1" role="img" aria-label="First hire photo"></span><div class="event-marker"><span class="pin"></span><span class="event-caption">First Hire</span></div></div>
    <div class="event"><span class="event-photo tone-2" role="img" aria-label="New shop photo"></span><div class="event-marker"><span class="pin"></span><span class="event-caption">New Shop</span></div></div>
    <div class="event"><span class="event-title">Crew of Five</span><span class="event-photo tone-3" role="img" aria-label="Crew photo"></span><div class="event-marker"><span class="pin"></span></div></div>
    <div class="event"><span class="event-photo tone-4" role="img" aria-label="Lamp retrofit photo"></span><div class="event-marker"><span class="pin"></span><span class="event-caption">Lamp Retrofit</span></div></div>
    <div class="event"><span class="event-photo tone-5" role="img" aria-label="City contract photo"></span><div class="event-marker"><span class="pin"></span><span class="event-caption">City Contract</span></div></div>
    <div class="event"><span class="event-title">Second Truck</span><span class="event-photo tone-6" role="img" aria-label="Truck photo"></span><div class="event-marker"><span class="pin"></span></div></div>
    <div class="event"><span class="event-photo tone-1" role="img" aria-label="Bucket lift photo"></span><div class="event-marker"><span class="pin"></span><span class="event-caption">Bucket Lift</span></div></div>
    <div class="event"><span class="event-photo tone-2" role="img" aria-label="Sign service photo"></span><div class="event-marker"><span class="pin"></span><span class="event-caption">Sign Service</span></div></div>
    <div class="event"><span class="event-title">Family Grows</span><span class="event-photo tone-3" role="img" aria-label="Family photo"></span><div class="event-marker"><span class="pin"></span></div></div>
    <div class="event"><span class="event-photo tone-4" role="img" aria-label="Warehouse photo"></span><div class="event-marker"><span class="pin"></span><span class="event-caption">New Warehouse</span></div></div>
    <div class="event"><span class="event-photo tone-5" role="img" aria-label="Mall photo"></span><div class="event-marker"><span class="pin"></span><span class="event-caption">Mall Contract</span></div></div>
    <div class="event"><span class="event-title">Parking Lots</span><span class="event-photo tone-6" role="img" aria-label="Parking lot lights photo"></span><div class="event-marker"><span class="pin"></span></div></div>
    <div class="event"><span class="event-photo tone-1" role="img" aria-label="Crew photo"></span><div class="event-marker"><span class="pin"></span><span class="event-caption">Crew of Ten</span></div></div>
    <div class="event"><span class="event-photo tone-2" role="img" aria-label="Award photo"></span><div class="event-marker"><span class="pin"></span><span class="event-caption">Safety Award</span></div></div>
    <div class="event"><span class="event-title">Ten Years</span><span class="event-photo tone-3" role="img" aria-label="Anniversary photo"></span><div class="event-marker"><span class="pin"></span></div></div>
    <div class="event"><span class="event-photo tone-4" role="img" aria-label="School photo"></span><div class="event-marker"><span class="pin"></span><span class="event-caption">School District</span></div></div>
    <div class="event"><span class="event-photo tone-5" role="img" aria-label="Office move photo"></span><div class="event-marker"><span class="pin"></span><span class="event-caption">Office Move</span></div></div>
    <div class="event"><span class="event-title">Y2K Ready</span><span class="event-photo tone-6" role="img" aria-label="Control room photo"></span><div class="event-marker"><span class="pin"></span></div></div>
  </div>
  <div class="year-band">
    <span class="gold">1983</span><span class="orange">1986</span><span class="yellow">1987</span><span class="red">1991</span><span class="red">1991</span><span class="red">1991</span><span class="red">1991</span><span class="yellow">1992</span><span class="magenta">1993</span><span class="blue">1994</span><span class="gold">1995</span><span class="gold">1995</span><span class="green">1996</span><span class="green">1996</span><span class="green">1996</span><span class="red">1997</span><span class="red">1997</span><span class="red">1997</span><span class="red">1997</span><span class="red">1997</span><span class="tan">1998</span><span class="pink">1999</span><span class="blue">2000</span><span class="blue">2000</span><span class="blue">2000</span>
  </div>
</section>

<section class="era era-2">
  <div class="event-strip">
    <div class="event"><span class="event-photo tone-1" role="img" aria-label="New sign photo"></span><div class="event-marker"><span class="pin"></span><span class="event-caption">New Look</span></div></div>
    <div class="event"><span class="event-photo tone-2" role="img" aria-label="Fleet photo"></span><div class="event-marker"><span class="pin"></span><span class="event-caption">Fleet Grows</span></div></div>
    <div class="event"><span class="event-title">Retail Chain</span><span class="event-photo tone-3" role="img" aria-label="Store photo"></span><div class="event-marker"><span class="pin"></span></div></div>
    <div class="event"><span class="event-photo tone-4" role="img" aria-label="Hospital photo"></span><div class="event-marker"><span class="pin"></span><span class="event-caption">Hospital Job</span></div></div>
    <div class="event"><span class="event-photo tone-5" role="img" aria-label="Staff photo"></span><div class="event-marker"><span class="pin"></span><span class="event-caption">Twenty Staff</span></div></div>
    <div class="event"><span class="event-title">Stadium Lights</span><span class="event-photo tone-6" role="img" aria-label="Stadium photo"></span><div class="event-marker"><span class="pin"></span></div></div>
    <div class="event"><span class="event-photo tone-1" role="img" aria-label="Night crew photo"></span><div class="event-marker"><span class="pin"></span><span class="event-caption">Night Crew</span></div></div>
    <div class="event"><span class="event-photo tone-2" role="img" aria-label="Ballast photo"></span><div class="event-marker"><span class="pin"></span><span class="event-caption">Ballast Recall</span></div></div>
    <div class="event"><span class="event-title">Storm Repair</span><span class="event-photo tone-3" role="img" aria-label="Storm repair photo"></span><div class="event-marker"><span class="pin"></span></div></div>
    <div class="event"><span class="event-photo tone-4" role="img" aria-label="LED test photo"></span><div class="event-marker"><span class="pin"></span><span class="event-caption">LED Trials</span></div></div>
    <div class="event"><span class="event-photo tone-5" role="img" aria-label="State contract photo"></span><div class="event-marker"><span class="pin"></span><span class="event-caption">State Contract</span></div></div>
    <div class="event"><span class="event-title">Second Branch</span><span class="event-photo tone-6" role="img" aria-label="Branch photo"></span><div class="event-marker"><span class="pin"></span></div></div>
    <div class="event"><span class="event-photo tone-1" role="img" aria-label="Training photo"></span><div class="event-marker"><span class="pin"></span><span class="event-caption">Training Room</span></div></div>
    <div class="event"><span class="event-photo tone-2" role="img" aria-label="Crane truck photo"></span><div class="event-marker"><span class="pin"></span><span class="event-caption">Crane Truck</span></div></div>
    <div class="event"><span class="event-title">Campus Work</span><span class="event-photo tone-3" role="img" aria-label="Campus photo"></span><div class="event-marker"><span class="pin"></span></div></div>
    <div class="event"><span class="event-photo tone-4" role="img" aria-label="Bridge photo"></span><div class="event-marker"><span class="pin"></span><span class="event-caption">Bridge Lights</span></div></div>
    <div class="event"><span class="event-photo tone-5" role="img" aria-label="Airport photo"></span><div class="event-marker"><span class="pin"></span><span class="event-caption">Airport Job</span></div></div>
    <div class="event"><span class="event-title">Twenty Years</span><span class="event-photo tone-6" role="img" aria-label="Anniversary photo"></span><div class="event-marker"><span class="pin"></span></div></div>
    <div class="event"><span class="event-photo tone-1" role="img" aria-label="Solar pole photo"></span><div class="event-marker"><span class="pin"></span><span class="event-caption">Solar Poles</span></div></div>
    <div class="event"><span class="event-photo tone-2" role="img" aria-label="Dispatch room photo"></span><div class="event-marker"><span class="pin"></span><span class="event-caption">New Dispatch</span></div></div>
    <div class="event"><span class="event-title">Highway Signs</span><span class="event-photo tone-3" role="img" aria-label="Highway photo"></span><div class="event-marker"><span class="pin"></span></div></div>
    <div class="event"><span class="event-photo tone-4" role="img" aria-label="Fleet photo"></span><div class="event-marker"><span class="pin"></span><span class="event-caption">Fleet of 30</span></div></div>
    <div class="event"><span class="event-photo tone-5" role="img" aria-label="Data center photo"></span><div class="event-marker"><span class="pin"></span><span class="event-caption">Data Center</span></div></div>
    <div class="event"><span class="event-title">Second Gen</span><span class="event-photo tone-6" role="img" aria-label="Family photo"></span><div class="event-marker"><span class="pin"></span></div></div>
  </div>
  <div class="year-band">
    <span class="blue">2000</span><span class="blue">2000</span><span class="orange">2001</span><span class="orange">2001</span><span class="orange">2001</span><span class="orange">2001</span><span class="orange">2001</span><span class="orange">2001</span><span class="orange">2001</span><span class="green">2002</span><span class="green">2002</span><span class="green">2002</span><span class="yellow">2003</span><span class="cyan">2004</span><span class="cyan">2004</span><span class="cyan">2004</span><span class="cyan">2004</span><span class="cyan">2004</span><span class="cyan">2004</span><span class="red">2005</span><span class="red">2005</span><span class="red">2005</span><span class="tan">2006</span><span class="tan">2006</span><span class="yellow">2007</span>
  </div>
</section>

<section class="era era-3">
  <div class="event-strip">
    <div class="event"><span class="event-photo tone-1" role="img" aria-label="Pledge photo"></span><div class="event-marker"><span class="pin"></span><span class="event-caption">Green Pledge</span></div></div>
    <div class="event"><span class="event-photo tone-2" role="img" aria-label="LED rollout photo"></span><div class="event-marker"><span class="pin"></span><span class="event-caption">LED Rollout</span></div></div>
    <div class="event"><span class="event-title">Bank Branches</span><span class="event-photo tone-3" role="img" aria-label="Bank photo"></span><div class="event-marker"><span class="pin"></span></div></div>
    <div class="event"><span class="event-photo tone-4" role="img" aria-label="Port photo"></span><div class="event-marker"><span class="pin"></span><span class="event-caption">Port Lighting</span></div></div>
    <div class="event"><span class="event-photo tone-5" role="img" aria-label="Rail yard photo"></span><div class="event-marker"><span class="pin"></span><span class="event-caption">Rail Yards</span></div></div>
    <div class="event"><span class="event-title">Van Upgrade</span><span class="event-photo tone-6" role="img" aria-label="Van photo"></span><div class="event-marker"><span class="pin"></span></div></div>
    <div class="event"><span class="event-photo tone-1" role="img" aria-label="Audit photo"></span><div class="event-marker"><span class="pin"></span><span class="event-caption">Energy Audit</span></div></div>
    <div class="event"><span class="event-photo tone-2" role="img" aria-label="Town square photo"></span><div class="event-marker"><span class="pin"></span><span class="event-caption">Town Square</span></div></div>
    <div class="event"><span class="event-title">Third Branch</span><span class="event-photo tone-3" role="img" aria-label="Branch photo"></span><div class="event-marker"><span class="pin"></span></div></div>
    <div class="event"><span class="event-photo tone-4" role="img" aria-label="Controls photo"></span><div class="event-marker"><span class="pin"></span><span class="event-caption">Smart Controls</span></div></div>
    <div class="event"><span class="event-photo tone-5" role="img" aria-label="Arena photo"></span><div class="event-marker"><span class="pin"></span><span class="event-caption">Arena Job</span></div></div>
    <div class="event"><span class="event-title">Warehouse Two</span><span class="event-photo tone-6" role="img" aria-label="Warehouse photo"></span><div class="event-marker"><span class="pin"></span></div></div>
    <div class="event"><span class="event-photo tone-1" role="img" aria-label="Holiday lights photo"></span><div class="event-marker"><span class="pin"></span><span class="event-caption">Tree Lighting</span></div></div>
    <div class="event"><span class="event-photo tone-2" role="img" aria-label="Staff photo"></span><div class="event-marker"><span class="pin"></span><span class="event-caption">Fifty Staff</span></div></div>
    <div class="event"><span class="event-title">Mall Retrofit</span><span class="event-photo tone-3" role="img" aria-label="Mall photo"></span><div class="event-marker"><span class="pin"></span></div></div>
    <div class="event"><span class="event-photo tone-4" role="img" aria-label="Crew photo"></span><div class="event-marker"><span class="pin"></span><span class="event-caption">Union Crew</span></div></div>
    <div class="event"><span class="event-photo tone-5" role="img" aria-label="Tower photo"></span><div class="event-marker"><span class="pin"></span><span class="event-caption">Tower Work</span></div></div>
    <div class="event"><span class="event-title">Site Survey</span><span class="event-photo tone-6" role="img" aria-label="Survey photo"></span><div class="event-marker"><span class="pin"></span></div></div>
    <div class="event"><span class="event-photo tone-1" role="img" aria-label="Grocery store photo"></span><div class="event-marker"><span class="pin"></span><span class="event-caption">Grocery Chain</span></div></div>
    <div class="event"><span class="event-photo tone-2" role="img" aria-label="Anniversary photo"></span><div class="event-marker"><span class="pin"></span><span class="event-caption">Thirty Years</span></div></div>
    <div class="event"><span class="event-title">New HQ</span><span class="event-photo tone-3" role="img" aria-label="Headquarters photo"></span><div class="event-marker"><span class="pin"></span></div></div>
    <div class="event"><span class="event-photo tone-4" role="img" aria-label="Service desk photo"></span><div class="event-marker"><span class="pin"></span><span class="event-caption">Service App</span></div></div>
    <div class="event"><span class="event-photo tone-5" role="img" aria-label="Depot photo"></span><div class="event-marker"><span class="pin"></span><span class="event-caption">Depot Opens</span></div></div>
    <div class="event"><span class="event-title">Award Night</span><span class="event-photo tone-6" role="img" aria-label="Award photo"></span><div class="event-marker"><span class="pin"></span></div></div>
  </div>
  <div class="year-band">
    <span class="yellow">2007</span><span class="yellow">2008</span><span class="yellow">2008</span><span class="yellow">2009</span><span class="yellow">2009</span><span class="teal">2010</span><span class="teal">2010</span><span class="teal">2010</span><span class="teal">2010</span><span class="orange">2011</span><span class="orange">2011</span><span class="orange">2011</span><span class="orange">2011</span><span class="orange">2011</span><span class="orange">2011</span><span class="orange">2011</span><span class="orange">2011</span><span class="orange">2011</span><span class="orange">2011</span><span class="blue">2012</span><span class="blue">2012</span><span class="blue">2012</span><span class="blue">2012</span><span class="blue">2012</span><span class="blue">2012</span>
  </div>
</section>

<section class="era era-4">
  <div class="event-strip">
    <div class="event"><span class="event-photo tone-1" role="img" aria-label="Hotel photo"></span><div class="event-marker"><span class="pin"></span><span class="event-caption">Hotel Chain</span></div></div>
    <div class="event"><span class="event-photo tone-2" role="img" aria-label="Park path photo"></span><div class="event-marker"><span class="pin"></span><span class="event-caption">Park Paths</span></div></div>
    <div class="event"><span class="event-title">Garage LEDs</span><span class="event-photo tone-3" role="img" aria-label="Garage photo"></span><div class="event-marker"><span class="pin"></span></div></div>
    <div class="event"><span class="event-photo tone-4" role="img" aria-label="Transit hub photo"></span><div class="event-marker"><span class="pin"></span><span class="event-caption">Transit Hub</span></div></div>
    <div class="event"><span class="event-photo tone-5" role="img" aria-label="Library photo"></span><div class="event-marker"><span class="pin"></span><span class="event-caption">Library Job</span></div></div>
    <div class="event"><span class="event-title">Factory Floor</span><span class="event-photo tone-6" role="img" aria-label="Factory photo"></span><div class="event-marker"><span class="pin"></span></div></div>
    <div class="event"><span class="event-photo tone-1" role="img" aria-label="Fleet tracking photo"></span><div class="event-marker"><span class="pin"></span><span class="event-caption">Fleet GPS</span></div></div>
    <div class="event"><span class="event-photo tone-2" role="img" aria-label="Museum photo"></span><div class="event-marker"><span class="pin"></span><span class="event-caption">Museum Job</span></div></div>
    <div class="event"><span class="event-title">Clinic Chain</span><span class="event-photo tone-3" role="img" aria-label="Clinic photo"></span><div class="event-marker"><span class="pin"></span></div></div>
    <div class="event"><span class="event-photo tone-4" role="img" aria-label="Sports park photo"></span><div class="event-marker"><span class="pin"></span><span class="event-caption">Sports Park</span></div></div>
    <div class="event"><span class="event-photo tone-5" role="img" aria-label="Bridge photo"></span><div class="event-marker"><span class="pin"></span><span class="event-caption">Bay Bridge</span></div></div>
    <div class="event"><span class="event-title">Campus Two</span><span class="event-photo tone-6" role="img" aria-label="Campus photo"></span><div class="event-marker"><span class="pin"></span></div></div>
    <div class="event"><span class="event-photo tone-1" role="img" aria-label="Retail hub photo"></span><div class="event-marker"><span class="pin"></span><span class="event-caption">Retail Hub</span></div></div>
    <div class="event"><span class="event-photo tone-2" role="img" aria-label="Office tower photo"></span><div class="event-marker"><span class="pin"></span><span class="event-caption">Office Tower</span></div></div>
    <div class="event"><span class="event-title">Pier Lights</span><span class="event-photo tone-3" role="img" aria-label="Pier photo"></span><div class="event-marker"><span class="pin"></span></div></div>
    <div class="event"><span class="event-photo tone-4" role="img" aria-label="Solar lot photo"></span><div class="event-marker"><span class="pin"></span><span class="event-caption">Solar Lots</span></div></div>
    <div class="event"><span class="event-photo tone-5" role="img" aria-label="Crew photo"></span><div class="event-marker"><span class="pin"></span><span class="event-caption">Crew of 80</span></div></div>
    <div class="event"><span class="event-title">Harbor Walk</span><span class="event-photo tone-6" role="img" aria-label="Harbor photo"></span><div class="event-marker"><span class="pin"></span></div></div>
    <div class="event"><span class="event-photo tone-1" role="img" aria-label="Plaza photo"></span><div class="event-marker"><span class="pin"></span><span class="event-caption">Plaza Job</span></div></div>
    <div class="event"><span class="event-photo tone-2" role="img" aria-label="Yard photo"></span><div class="event-marker"><span class="pin"></span><span class="event-caption">Yard Expands</span></div></div>
    <div class="event"><span class="event-title">County Deal</span><span class="event-photo tone-3" role="img" aria-label="County contract photo"></span><div class="event-marker"><span class="pin"></span></div></div>
    <div class="event"><span class="event-photo tone-4" role="img" aria-label="Truck photo"></span><div class="event-marker"><span class="pin"></span><span class="event-caption">New Trucks</span></div></div>
    <div class="event"><span class="event-photo tone-5" role="img" aria-label="Team photo"></span><div class="event-marker"><span class="pin"></span><span class="event-caption">Team Photo</span></div></div>
    <div class="event"><span class="event-title">Next Chapter</span><span class="event-photo tone-6" role="img" aria-label="Office exterior photo"></span><div class="event-marker"><span class="pin"></span></div></div>
  </div>
  <div class="year-band">
    <span class="blue">2012</span><span class="blue">2012</span><span class="blue">2012</span><span class="blue">2012</span><span class="blue">2012</span><span class="gold">2013</span><span class="gold">2013</span><span class="gold">2013</span><span class="gold">2013</span><span class="gold">2013</span><span class="gold">2013</span><span class="gold">2013</span><span class="gold">2013</span><span class="gold">2014</span><span class="gold">2014</span><span class="gold">2014</span><span class="gold">2014</span><span class="gold">2014</span><span class="gold">2014</span><span class="gold">2014</span><span class="gold">2014</span><span class="gold">2014</span><span class="gold">2014</span><span class="gold">2014</span><span class="gold">2014</span>
  </div>
</section>

</main>
</body>
</html>
```